Italian restaurant needs new site

Need to make our website better.

Must have reservation module

Must be able to sell wine tasting tours and wine pairing tours and intégrate with dunmo desk

Blog

Social media

Wandervane ranking and last review.
Updates

Number of Pages Required

1 page

Font styles to use
Serif

Requirements
Must have
• Reservation module
• Marketplace to buy wine pairings and gift certificates
• Wandervane review
• Kindlepost posts
• All info from old site

```html
<!DOCTYPE html>
<html lang="en">
<head>
<meta charset="utf-8">
<title>Verdello — Italian Restaurant</title>
<link href="https://fonts.googleapis.com/css2?family=Kaushan+Script&family=Cabin+Sketch:wght@700&family=Oswald:wght@500;700&family=Montserrat:wght@400;600;700&family=Open+Sans:wght@400;600&family=Playfair+Display:wght@700&display=swap" rel="stylesheet">
<style>
:root{
  --ink:#2b2b2b;
  --muted:#777;
  --line:#e4e4e4;
  --slate:#30353b;
  --slate-deep:#262a2f;
  --orange:#f0a44c;
  --orange-deep:#e8912e;
  --red:#c4262e;
  --price:#e39a3a;
  --paper:#ffffff;
  --footer:#353535;
  --footer-text:#b9b9b9;
}
*{box-sizing:border-box;margin:0;padding:0}
html,body{width:1200px;height:4580px;overflow:hidden;background:var(--paper)}
body{font-family:"Open Sans",Arial,sans-serif;color:var(--ink);position:relative}
.abs{position:absolute}

/* hero */
.hero{position:absolute;left:0;top:0;width:1200px;height:700px;
  background:radial-gradient(ellipse at 50% 45%,#3a4047 0%,var(--slate) 55%,var(--slate-deep) 100%)}
.hero-food{position:absolute;border-radius:50%;background:radial-gradient(circle,#8a5a3a,#4a3326)}
.brand-corner{position:absolute;left:0;top:0;width:130px;height:128px;background:#f3efe9;
  display:flex;flex-direction:column;align-items:center;justify-content:center;gap:6px}
.brand-corner .name{font-family:"Playfair Display",serif;font-size:26px;color:#3a3a3a}
.brand-corner .tag{font-family:"Montserrat",sans-serif;font-size:8px;letter-spacing:1px;color:#777}
.nav{position:absolute;top:34px;left:0;width:1200px;display:flex;justify-content:center;align-items:center;gap:30px;
  font-family:"Montserrat",sans-serif;font-size:11px;font-weight:600;letter-spacing:1px;color:#fff}
.nav .on{color:var(--orange)}
.nav .logo{font-family:"Kaushan Script",cursive;font-size:32px;letter-spacing:0;font-weight:400;margin:0 40px}
.hero-kicker{position:absolute;top:240px;width:1200px;text-align:center;font-family:"Kaushan Script",cursive;font-size:30px;color:#fff}
.hero-title{position:absolute;top:285px;width:1200px;text-align:center;font-family:"Cabin Sketch",cursive;font-size:64px;letter-spacing:4px;color:#fff}
.hero-since{position:absolute;top:362px;width:1200px;text-align:center;font-family:"Montserrat",sans-serif;font-size:11px;letter-spacing:3px;color:#ddd}
.hero-btn{position:absolute;top:388px;left:540px;width:120px;height:34px;background:var(--orange);color:#fff;
  font-family:"Montserrat",sans-serif;font-size:11px;font-weight:700;letter-spacing:1px;display:flex;align-items:center;justify-content:center}
.hero-tab{position:absolute;top:660px;left:560px;width:80px;height:40px;background:#fff;border-radius:40px 40px 0 0;display:flex;align-items:center;justify-content:center}

/* reservation */
.reserve-title{position:absolute;top:740px;width:1200px;text-align:center;font-family:"Montserrat",sans-serif;font-size:12px;letter-spacing:3px;color:#666}
.reserve-power{position:absolute;top:780px;width:1200px;text-align:center;font-size:8px;letter-spacing:1px;color:#999}
.field{position:absolute;top:840px;height:34px;display:flex;align-items:center;gap:14px;font-size:14px;color:#444}
.field .box{border:1px solid #ccc;height:34px;display:flex;align-items:center;justify-content:space-between;padding:0 10px}
.find-btn{position:absolute;top:912px;left:484px;width:232px;height:36px;background:#1f1f1f;color:#fff;
  font-family:"Montserrat",sans-serif;font-size:12px;font-weight:700;letter-spacing:2px;display:flex;align-items:center;justify-content:center}
.rule{position:absolute;left:30px;width:1140px;height:1px;background:var(--line)}
.notice{position:absolute;top:1028px;left:130px;width:940px;text-align:center;font-size:14px;line-height:26px;color:#444}

/* featured */
.feat-kicker{position:absolute;top:1110px;width:1200px;text-align:center;font-family:"Kaushan Script",cursive;font-size:14px;color:var(--orange)}
.feat-title{position:absolute;top:1134px;width:1200px;text-align:center;font-family:"Montserrat",sans-serif;font-size:20px;font-weight:700;color:#222}
.feat-tabs{position:absolute;top:1170px;width:1200px;display:flex;justify-content:center;gap:22px;font-family:"Montserrat",sans-serif;font-size:9px;letter-spacing:1px;color:#888}
.feat-tabs .on{color:var(--orange)}
.card{position:absolute;width:285px;height:390px;border:1px solid #eee;background:#fff;text-align:center}
.card.lift{box-shadow:0 6px 22px rgba(0,0,0,.14);border-color:#fff}
.card .photo{position:absolute;left:30px;top:40px;width:225px;height:200px;border-radius:8px}
.card .stars{position:absolute;top:280px;width:100%;font-size:11px;letter-spacing:2px;color:var(--orange)}
.card .name{position:absolute;top:326px;width:100%;font-family:"Montserrat",sans-serif;font-size:12px;letter-spacing:1px;color:#333}
.card .price{position:absolute;top:352px;width:100%;font-size:12px;color:var(--orange)}
.card .actions{position:absolute;left:0;bottom:0;width:100%;height:72px;display:flex}
.card .actions span{flex:1;background:var(--orange);display:flex;align-items:center;justify-content:center;border-right:1px solid rgba(255,255,255,.35);color:#fff;font-size:9px;font-family:"Montserrat",sans-serif;font-weight:700}
.card .actions span.dark{background:#2b2b2b;flex:1.6}
.badge{position:absolute;left:0;top:0;width:0;height:0;border-top:44px solid var(--red);border-right:44px solid transparent}

/* specialties */
.special{position:absolute;top:2162px;left:0;width:1200px;height:488px;
  background:radial-gradient(ellipse at 50% 50%,#3b4148 0%,var(--slate) 55%,var(--slate-deep) 100%)}
.special h2{position:absolute;top:220px;width:1200px;text-align:center;font-family:"Cabin Sketch",cursive;font-size:48px;letter-spacing:3px;color:#fff;font-weight:700}

/* menu */
.menu-frame{position:absolute;top:2690px;left:55px;width:1130px;height:1355px;border:2px solid #555}
.menu-title{position:absolute;top:2688px;left:460px;width:280px;height:60px;background:#fff;text-align:center;
  font-family:"Kaushan Script",cursive;font-size:48px;line-height:54px;color:#222;transform:translateY(-26px)}
.dish{position:absolute;width:640px}
.dish .row{display:flex;align-items:baseline;gap:6px}
.dish .nm{font-family:"Oswald",sans-serif;font-weight:700;font-size:30px;color:var(--red);letter-spacing:1px;white-space:nowrap}
.dish .dots{flex:1;border-bottom:4px dotted var(--red);transform:translateY(-6px)}
.dish .pr{font-family:"Kaushan Script",cursive;font-size:36px;color:var(--price);white-space:nowrap}
.dish p{font-family:"Montserrat",sans-serif;font-size:13px;line-height:17px;color:#222;margin-top:2px;width:520px}
.menu-rule{position:absolute;top:3328px;left:110px;width:1020px;height:1px;background:#ddd}
.art{position:absolute}

/* gallery strip */
.strip{position:absolute;top:4064px;left:0;width:1200px;height:210px;display:flex}
.strip .tile{width:300px;height:210px;position:relative;overflow:hidden}
.strip .board{background:var(--slate);color:#ccc;text-align:center}
.board .logo{font-family:"Kaushan Script",cursive;font-size:28px;color:#fff;margin-top:22px}
.board p{font-size:8px;line-height:12px;width:230px;margin:10px auto 0}
.tile .cap{position:absolute;left:20px;font-family:"Playfair Display",serif}

/* footer */
.footer{position:absolute;top:4274px;left:0;width:1200px;height:306px;background:var(--footer);color:var(--footer-text);font-size:9px;line-height:15px}
.fcol{position:absolute;top:60px}
.fcol h4{font-family:"Montserrat",sans-serif;font-size:11px;letter-spacing:1px;color:#fff;margin-bottom:16px}
.fcol b{color:#ddd;font-weight:600}
.tags{display:grid;grid-template-columns:repeat(3,auto);gap:6px;width:150px}
.tags span{border:1px solid #666;padding:1px 5px;font-size:8px}
.links{display:grid;grid-template-columns:90px 90px;row-gap:6px}
.hours div{display:flex;justify-content:space-between;width:170px}
.hours .open{margin-top:18px;width:150px;border:1px solid #777;padding:8px;text-align:center}
.hours .open em{font-family:"Kaushan Script",cursive;font-style:normal;color:#fff;font-size:13px;display:block}
</style>
</head>
<body>

<section class="hero">
  <div class="hero-food" role="img" aria-label="Macarons and bread on a dark table" style="left:-40px;top:140px;width:180px;height:260px;border-radius:40%;background:radial-gradient(circle,#b86e7a,#5a3a3a)"></div>
  <div class="hero-food" role="img" aria-label="Wine glasses in the corner" style="left:1060px;top:-40px;width:180px;height:200px;background:radial-gradient(circle,#6a5a58,#3a3335)"></div>
  <div class="hero-food" role="img" aria-label="Board with sliced meats" style="left:-40px;top:430px;width:260px;height:260px;background:radial-gradient(circle,#9c6a48,#4a3326)"></div>
  <div class="hero-food" role="img" aria-label="Cheese and peppers" style="left:940px;top:400px;width:300px;height:300px;background:radial-gradient(circle,#c08a4a,#4a3a2a)"></div>
  <div class="hero-food" role="img" aria-label="Nuts and fruit" style="left:560px;top:560px;width:180px;height:120px;background:radial-gradient(circle,#8a6040,#3a3028)"></div>

  <div class="brand-corner"><span class="name">Vinora</span><span class="tag">RISTORANTE &amp; VINO</span></div>

  <nav class="nav">
    <span class="on">HOME</span><span>OUR STORY</span><span>SHOP</span>
    <span class="logo">Verdello</span>
    <span>MENU</span><span>BLOG</span><span>CONTACT</span>
    <svg width="12" height="12" viewBox="0 0 12 12"><circle cx="5" cy="5" r="4" fill="none" stroke="#fff" stroke-width="1.5"/><line x1="8" y1="8" x2="11" y2="11" stroke="#fff" stroke-width="1.5"/></svg>
  </nav>

  <div class="hero-kicker">Different types of</div>
  <h1 class="hero-title">ITALIAN CUISINE</h1>
  <div class="hero-since">SINCE 1990</div>
  <div class="hero-btn">ORDER NOW</div>

  <div class="hero-tab"><svg width="20" height="12" viewBox="0 0 20 12"><polyline points="2,2 10,10 18,2" fill="none" stroke="#333" stroke-width="3"/></svg></div>
</section>

<section class="reservation">
  <div class="reserve-title">MAKE A RESERVATION</div>
  <div class="reserve-power">POWERED BY TABLENEST</div>

  <div class="field" style="left:268px">
    <svg width="14" height="14" viewBox="0 0 14 14"><rect x="1" y="2" width="12" height="11" fill="none" stroke="#555"/><line x1="1" y1="5" x2="13" y2="5" stroke="#555"/></svg>
    <div class="box" style="width:140px">08/05/2017</div>
  </div>
  <div class="field" style="left:505px">
    <svg width="14" height="14" viewBox="0 0 14 14"><circle cx="7" cy="7" r="6" fill="none" stroke="#555"/><polyline points="7,3 7,7 10,8" fill="none" stroke="#555"/></svg>
    <div class="box" style="width:170px">7:00 pm <span>▾</span></div>
  </div>
  <div class="field" style="left:755px">
    <svg width="14" height="14" viewBox="0 0 14 14"><circle cx="7" cy="4" r="3" fill="#555"/><path d="M1 13 Q7 5 13 13Z" fill="#555"/></svg>
    <div class="box" style="width:150px">2 People <span>▾</span></div>
  </div>
  <div class="find-btn">FIND A TABLE</div>
  <div class="rule" style="top:992px"></div>
  <p class="notice">Due to the limited amount of tables in our restaurant, we cannot guarantee a private table. Some reservations will be sat at the bar or communal. If you prefer a table, please call or make a note and we will do our best to accommodate your request.</p>
  <svg class="abs" style="left:590px;top:1076px" width="20" height="10" viewBox="0 0 20 10"><line x1="0" y1="5" x2="20" y2="5" stroke="#bbb"/><circle cx="10" cy="5" r="2" fill="#bbb"/></svg>
</section>

<section class="featured">
  <svg class="abs" style="left:586px;top:1084px" width="28" height="22" viewBox="0 0 28 22"><path d="M4 16 Q14 2 24 16Z" fill="none" stroke="#999" stroke-width="1.5"/><line x1="2" y1="18" x2="26" y2="18" stroke="#999" stroke-width="1.5"/></svg>
  <div class="feat-kicker">Organic products</div>
  <h2 class="feat-title">FEATURED PRODUCTS</h2>
  <div class="feat-tabs"><span class="on">ALL PRODUCTS</span><span>/</span><span>BREADS</span><span>/</span><span>CAKES</span><span>/</span><span>COOKIES</span><span>/</span><span>FLOUR</span><span>/</span><span>OTHER</span></div>

  <article class="card" style="left:15px;top:1325px"><div class="photo" role="img" aria-label="Row of small cookie bags" style="background:linear-gradient(135deg,#f1e4d3,#c8a27a)"></div><div class="stars">★★★★☆</div><div class="name">COOKIES COMBO</div><div class="price">$10.00</div></article>
  <article class="card lift" style="left:314px;top:1325px"><div class="badge"></div><div class="photo" role="img" aria-label="Sliced pizza on a wooden board" style="top:20px;background:linear-gradient(135deg,#f4c77a,#c8522e)"></div><div class="stars" style="top:240px">★★★★☆</div><div class="name" style="top:280px">SWEET BUNS</div><div class="price" style="top:300px">$10.00</div><div class="actions"><span><svg width="14" height="14" viewBox="0 0 14 14"><circle cx="6" cy="6" r="4.5" fill="none" stroke="#fff" stroke-width="1.5"/><line x1="9" y1="9" x2="13" y2="13" stroke="#fff" stroke-width="1.5"/></svg></span><span class="dark">ADD TO CART</span><span>♥</span><span><svg width="14" height="14" viewBox="0 0 14 14"><polyline points="1,12 5,7 8,9 13,2" fill="none" stroke="#fff" stroke-width="1.5"/></svg></span></div></article>
  <article class="card" style="left:607px;top:1325px"><div class="photo" role="img" aria-label="Tomatoes, mozzarella and basil on a board" style="background:linear-gradient(90deg,#7aa35a,#f1efe8 50%,#d2452f)"></div><div class="stars">★★★★☆</div><div class="name">CINNAMON BUNS</div><div class="price">$10.00</div></article>
  <article class="card" style="left:900px;top:1325px"><div class="photo" role="img" aria-label="Assorted bread loaves" style="background:linear-gradient(135deg,#e0b98a,#8a5a36)"></div><div class="stars">★★★★☆</div><div class="name">BROWN BREADS COMBO</div><div class="price">$10.00</div></article>

  <article class="card" style="left:15px;top:1731px"><div class="photo" role="img" aria-label="Olive oil bottle and olives on a board" style="background:linear-gradient(135deg,#d9c07a,#6d7a3a)"></div><div class="stars">★★★★☆</div><div class="name">CHOCOLATE CHIP COOKIES</div><div class="price">$10.00</div></article>
  <article class="card" style="left:314px;top:1731px"><div class="photo" role="img" aria-label="Sack of flour with wheat" style="background:linear-gradient(135deg,#f3ead8,#c9a46a)"></div><div class="stars">★★★★☆</div><div class="name">BAKING FLOUR</div><div class="price">$10.00</div></article>
  <article class="card" style="left:607px;top:1731px"><div class="photo" role="img" aria-label="Pizza slices" style="background:linear-gradient(135deg,#f4c77a,#c8522e)"></div><div class="stars">★★★★☆</div><div class="name">SWEET ALMONDS</div><div class="price">$10.00</div></article>
  <article class="card" style="left:900px;top:1731px"><div class="photo" role="img" aria-label="Cup of chocolate ice cream" style="background:linear-gradient(135deg,#e8dcc8,#5a3a28)"></div><div class="stars">★★★★☆</div><div class="name">COOKIE ICE CREAM</div><div class="price">$10.00</div></article>
</section>

<section class="special" role="img" aria-label="Dark table with ingredients around the edges">
  <div class="hero-food" style="left:-40px;top:0;width:200px;height:220px;background:radial-gradient(circle,#9a6a4a,#3a2e28)"></div>
  <div class="hero-food" style="left:-30px;top:280px;width:200px;height:220px;background:radial-gradient(circle,#b86e7a,#4a3436)"></div>
  <div class="hero-food" style="left:1000px;top:20px;width:220px;height:200px;background:radial-gradient(circle,#c08a4a,#3a3028)"></div>
  <div class="hero-food" style="left:980px;top:280px;width:240px;height:220px;background:radial-gradient(circle,#d0a870,#403228)"></div>
  <h2>OUR SPECIALTIES</h2>
</section>

<section class="menu">
  <div class="menu-frame"></div>
  <h2 class="menu-title">OUR MENU</h2>

  <div class="art" role="img" aria-label="Two margherita pizzas" style="left:824px;top:2693px;width:350px;height:360px;border-radius:50%;background:radial-gradient(circle,#e85a3a 0%,#d9a050 70%,rgba(255,255,255,0) 72%)"></div>
  <div class="art" role="img" aria-label="Fork lifting a pizza slice" style="left:0;top:3282px;width:351px;height:305px;border-radius:50%;background:radial-gradient(circle,#e46a40 0%,#e0b070 65%,rgba(255,255,255,0) 68%)"></div>
  <div class="art" role="img" aria-label="Wine bottle, cheese and tomatoes" style="left:0;top:3740px;width:305px;height:290px;background:radial-gradient(ellipse at 40% 60%,#f2c84a 0%,#8a2a2a 45%,rgba(255,255,255,0) 70%)"></div>
  <div class="art" role="img" aria-label="Fresh pasta nests with basil and tomatoes" style="left:641px;top:3786px;width:534px;height:274px;background:radial-gradient(ellipse at 55% 65%,#f0d27a 0%,#5a8a3a 40%,rgba(255,255,255,0) 70%)"></div>

  <div class="dish" style="left:113px;top:2832px"><div class="row"><span class="nm">LOREM IPSUM</span><span class="dots"></span><span class="pr">$13.99</span></div><p>Lorem ipsum dolor sit amet, consectetur adipiscing elit. Duis molestie nulla mod met, nec dapibus Lorem ipsum dolor sit amet, consectetur adipiscing elit.</p></div>
  <div class="dish" style="left:113px;top:2924px"><div class="row"><span class="nm">LOREM IPSUM</span><span class="dots"></span><span class="pr">$13.99</span></div><p>Lorem ipsum dolor sit amet, consectetur adipiscing elit. Duis molestie nulla mod met, nec dapibus Lorem ipsum dolor sit amet, consectetur adipiscing elit.</p></div>
  <div class="dish" style="left:113px;top:3016px"><div class="row"><span class="nm">LOREM IPSUM</span><span class="dots"></span><span class="pr">$13.99</span></div><p>Lorem ipsum dolor sit amet, consectetur adipiscing elit. Duis molestie nulla mod met, nec dapibus Lorem ipsum dolor sit amet, consectetur adipiscing elit.</p></div>
  <div class="dish" style="left:113px;top:3102px"><div class="row"><span class="nm">LOREM IPSUM</span><span class="dots"></span><span class="pr">$13.99</span></div><p>Lorem ipsum dolor sit amet, consectetur adipiscing elit. Duis molestie nulla mod met, nec dapibus Lorem ipsum dolor sit amet, consectetur adipiscing elit.</p></div>
  <div class="dish" style="left:113px;top:3188px"><div class="row"><span class="nm">LOREM IPSUM</span><span class="dots"></span><span class="pr">$13.99</span></div><p>Lorem ipsum dolor sit amet, consectetur adipiscing elit. Duis molestie nulla mod met, nec dapibus Lorem ipsum dolor sit amet, consectetur adipiscing elit.</p></div>

  <div class="menu-rule"></div>

  <div class="dish" style="left:464px;top:3367px"><div class="row"><span class="nm">LOREM IPSUM</span><span class="dots"></span><span class="pr">$13.99</span></div><p>Lorem ipsum dolor sit amet, consectetur adipiscing elit. Duis molestie nulla mod met, nec dapibus Lorem ipsum dolor sit amet, consectetur adipiscing elit.</p></div>
  <div class="dish" style="left:464px;top:3449px"><div class="row"><span class="nm">LOREM IPSUM</span><span class="dots"></span><span class="pr">$13.99</span></div><p>Lorem ipsum dolor sit amet, consectetur adipiscing elit. Duis molestie nulla mod met, nec dapibus Lorem ipsum dolor sit amet, consectetur adipiscing elit.</p></div>
  <div class="dish" style="left:464px;top:3538px"><div class="row"><span class="nm">LOREM IPSUM</span><span class="dots"></span><span class="pr">$13.99</span></div><p>Lorem ipsum dolor sit amet, consectetur adipiscing elit. Duis molestie nulla mod met, nec dapibus Lorem ipsum dolor sit amet, consectetur adipiscing elit.</p></div>
  <div class="dish" style="left:464px;top:3623px"><div class="row"><span class="nm">LOREM IPSUM</span><span class="dots"></span><span class="pr">$13.99</span></div><p>Lorem ipsum dolor sit amet, consectetur adipiscing elit. Duis molestie nulla mod met, nec dapibus Lorem ipsum dolor sit amet, consectetur adipiscing elit.</p></div>
  <div class="dish" style="left:464px;top:3709px"><div class="row"><span class="nm">LOREM IPSUM</span><span class="dots"></span><span class="pr">$13.99</span></div><p>Lorem ipsum dolor sit amet, consectetur adipiscing elit. Duis molestie nulla mod met, nec dapibus Lorem ipsum dolor sit amet, consectetur adipiscing elit.</p></div>
</section>

<section class="strip">
  <div class="tile" role="img" aria-label="Roast meat on a white plate" style="background:linear-gradient(135deg,#f4f1ec 40%,#7a4a30)">
    <span class="cap" style="top:130px;font-size:10px;color:#777">The taste of</span>
    <span class="cap" style="top:146px;font-size:20px;color:var(--orange)">WINTER AUTUMN</span>
  </div>
  <div class="tile board"><div class="logo">Verdello</div><p>Fresh seasonal dishes made daily from local farms, slow sauces and bread baked each morning in our own oven.</p></div>
  <div class="tile" role="img" aria-label="Hand holding a bread roll" style="background:linear-gradient(90deg,#f6f3ef 45%,#c89a6a)">
    <span class="cap" style="top:78px;font-size:10px;color:#888">A taste of the</span>
    <span class="cap" style="top:94px;font-size:24px;color:#333">GOOD LIFE</span>
  </div>
  <div class="tile board"><div class="logo">Verdello</div><p>Fresh seasonal dishes made daily from local farms, slow sauces and bread baked each morning in our own oven.</p></div>
</section>

<footer class="footer">
  <div class="fcol" style="left:235px"><h4>CONTACT</h4>
    <b>Paris</b><br>18 Rue Verdelle, 75004 Paris<br>+33 1 40 55 21 90<br>hello@verdello.test<br><br>
    <b>Rome</b><br>Via del Corso 41, Roma<br>+39 06 4411 2203<br>roma@verdello.test
  </div>
  <div class="fcol" style="left:424px"><h4>POPULAR TAGS</h4>
    <div class="tags"><span>Fruit</span><span>Vegetables</span><span>Bread</span><span>Wine tours</span><span>Pasta</span><span>Organic</span><span>Dessert</span><span>Pizza</span></div>
  </div>
  <div class="fcol" style="left:607px"><h4>USEFUL LINK</h4>
    <div class="links"><span>My account</span><span>Team</span><span>Discount</span><span>Careers</span><span>New products</span><span>Best sellers</span><span>Top sellers</span><span>FAQ</span><span>Wishlist</span><span>Payment</span><span>Best products</span></div>
  </div>
  <div class="fcol hours" style="left:800px"><h4>WORKING TIME</h4>
    <div><span>Monday to Friday</span><b>08:00am - 09:00pm</b></div>
    <div><span>Saturday &amp; Sunday</span><b>10:00am - 08:00pm</b></div>
    <div class="open"><em>Happy Hours</em>Daily aperitivo hour<br><b>04:00 pm - 06:00 pm</b></div>
  </div>
</footer>

</body>
</html>
```